Business Card Design and Logo Needed

I need Business Cards and a Logo for my website and public speaking business which can be found at: www.corvina-lett.example

I'm looking for creative and unique ideas. Some business cards I've found online that I like can be found at:
http://gigbarrow.example/general/18-smokin-hot-business-card-designs/

and at

http://www.plumquarry.example/2009/04/50-creative-business-cards-of-50-graphic-designers/

```html
<!DOCTYPE html>
<html lang="en">
<head>
<meta charset="utf-8">
<title>Corvina Lett – Business Card</title>
<link rel="stylesheet" href="https://fonts.googleapis.com/css2?family=Raleway:wght@200&family=PT+Sans:ital,wght@0,400;0,700;1,400&display=swap">
<style>
  :root {
    --olive-dark: #3d5212;
    --olive-faint: #4c6620;
    --olive-mid: #5c7a1e;
    --olive-text: #4b6614;
    --olive-light: #7a9a2e;
    --tagline: #a9b88a;
    --paper: #ffffff;
  }
  html, body {
    margin: 0;
    padding: 0;
    width: 1200px;
    height: 900px;
    overflow: hidden;
    background: var(--paper);
  }
  .canvas {
    position: relative;
    width: 1200px;
    height: 900px;
    background: var(--paper);
  }
  .card {
    position: absolute;
    top: 36px;
    width: 412px;
    height: 826px;
    box-sizing: border-box;
    overflow: hidden;
  }
  .card--back {
    left: 128px;
    background: var(--olive-dark);
  }
  .card--front {
    left: 670px;
    background: var(--paper);
    border: 2px solid var(--olive-mid);
  }
  .back-mark {
    position: absolute;
    left: 0;
    right: 0;
    top: 300px;
    text-align: center;
    font-family: "PT Sans", sans-serif;
    font-size: 58px;
    color: var(--olive-faint);
    margin: 0;
  }
  .tagline {
    position: absolute;
    left: 44px;
    top: 675px;
    margin: 0;
    font-family: "PT Sans", sans-serif;
    font-size: 23px;
    color: var(--tagline);
    letter-spacing: 0.2px;
  }
  .name {
    position: absolute;
    left: 38px;
    top: 550px;
    margin: 0;
    transform: rotate(-90deg);
    transform-origin: left top;
    font-family: "Raleway", sans-serif;
    font-weight: 200;
    font-size: 76px;
    line-height: 1;
    color: var(--olive-mid);
    white-space: nowrap;
    letter-spacing: -1px;
  }
  .role {
    position: absolute;
    left: 124px;
    top: 186px;
    margin: 0;
    transform: rotate(-90deg);
    transform-origin: left top;
    font-family: "PT Sans", sans-serif;
    font-style: italic;
    font-size: 21px;
    line-height: 1;
    color: var(--olive-light);
    white-space: nowrap;
  }
  .brand-name {
    position: absolute;
    right: 44px;
    top: 606px;
    margin: 0;
    font-family: "PT Sans", sans-serif;
    font-size: 22px;
    color: var(--olive-light);
  }
  .contact {
    position: absolute;
    right: 44px;
    top: 672px;
    margin: 0;
    text-align: right;
    font-family: "PT Sans", sans-serif;
    font-style: normal;
  }
  .contact__phone {
    display: block;
    font-weight: 700;
    font-size: 25px;
    color: var(--olive-text);
    margin-bottom: 8px;
  }
  .contact__line {
    display: block;
    font-size: 22px;
    color: var(--olive-light);
    margin-bottom: 10px;
  }
</style>
</head>
<body>
  <main class="canvas">
    <section class="card card--back" aria-label="Card back">
      <p class="back-mark">Corvina Lett</p>
      <p class="tagline">wonder. explore. dream. achieve</p>
    </section>

    <section class="card card--front" aria-label="Card front">
      <h1 class="name">CORVINALETT</h1>
      <p class="role">public speaker</p>
      <p class="brand-name">Corvina Lett</p>
      <address class="contact">
        <span class="contact__phone">0172 380 415</span>
        <span class="contact__line">corvina@corvina-lett.example</span>
        <span class="contact__line">www.corvina-lett.example</span>
      </address>
    </section>
  </main>
</body>
</html>
```